We are Larkmoor Cardiology and Vascular Medicine and located at 4512 Colby Road, Suites 300 & 400, Winchester, VA 22601. Our phone is 540-555-0187 We are creating a brochure to promote our Arrhythmia Clinic. Our audience is both patients and referring to help education and understand our arrhythmias. Please add imaging. We appreciate any create suggestions when comes to imaging as long as relates to medical information being provided.

```html
<!DOCTYPE html>
<html lang="en">
<head>
<meta charset="utf-8">
<title>Arrhythmias Brochure – Larkmoor Cardiology</title>
<link href="https://fonts.googleapis.com/css2?family=Poppins:wght@400;500;600;700&family=Oswald:wght@600;700&display=swap" rel="stylesheet">
<style>
:root{
  --bg:#e6e6e8;
  --crimson:#c9223f;
  --wine:#8d1c33;
  --deep:#5e1027;
  --blue:#1b6cb6;
  --purple:#6b3b8f;
  --coral:#f26a76;
  --bullet:#f0506a;
  --white:#ffffff;
  --ink:#222;
}
*{box-sizing:border-box;margin:0;padding:0}
html,body{width:1200px;height:900px;overflow:hidden}
body{background:var(--bg);font-family:'Poppins',sans-serif;color:var(--ink);position:relative}
.spread{position:absolute;left:30px;width:1140px;height:420px;display:flex;box-shadow:0 6px 18px rgba(0,0,0,.18)}
.spread--outside{top:20px}
.spread--inside{top:460px}
.panel{width:380px;height:100%;position:relative;overflow:hidden}
ul{list-style:none}
.bullets li{position:relative;padding-left:13px}
.bullets li::before{content:"";position:absolute;left:0;top:.35em;width:7px;height:7px;border-radius:50%;background:var(--bullet)}
.bullets--blue li::before{background:var(--blue)}
.bullets--soft li::before{background:#f28a98}
b{font-weight:600}

/* outside: treatments detail */
.panel--treat-detail{background:var(--white);padding:16px 22px 30px;font-size:7.6px;line-height:1.28}
.panel--treat-detail h3{color:var(--crimson);font-size:12px;font-weight:600;margin:0 0 3px}
.panel--treat-detail li{margin-bottom:3px}
.panel--treat-detail .group{border-bottom:1px solid #f1a7b3;padding-bottom:5px;margin-bottom:7px}
.panel--treat-detail .group:last-child{border:none}
.strip{position:absolute;left:0;right:0;bottom:0;height:18px;background:var(--crimson)}

/* outside: about */
.panel--about{color:var(--white)}
.photo{position:absolute;inset:0}
.photo--chest{background:radial-gradient(circle at 48% 52%,#e43a4f 0%,#a6203a 28%,#3b2f82 62%,#241d4a 100%)}
.about-overlay{position:absolute;inset:0;background:linear-gradient(180deg,rgba(110,15,35,.72),rgba(90,10,30,.82))}
.about-body{position:absolute;left:32px;top:50px;width:210px;font-size:7.5px;line-height:1.3}
.about-body h2{font-size:15px;font-weight:600;line-height:1.15;margin-bottom:8px}
.about-body h2 span{color:var(--coral);display:block}
.about-body h4{font-size:9px;font-weight:500;margin:6px 0 2px}
.about-body .rule{border-top:1px solid rgba(255,255,255,.35);margin:8px 0 4px}
.about-body li{padding-left:30px;margin-bottom:1px}
.about-body li::before{left:0}
.about-foot{position:absolute;left:0;right:0;bottom:18px;height:48px;background:var(--wine);font-size:6.8px;line-height:1.3;padding:9px 32px}
.ghost{position:absolute;font-family:'Oswald',sans-serif;font-weight:700;color:rgba(255,255,255,.12);font-size:78px;letter-spacing:1px;white-space:nowrap}

/* cover */
.panel--cover .vertical{position:absolute;right:22px;top:28px;height:310px;writing-mode:vertical-rl;transform:rotate(180deg);font-family:'Oswald',sans-serif;font-weight:700;font-size:50px;color:var(--white);line-height:1;text-align:left;white-space:nowrap}
.phone-bar{position:absolute;left:0;right:0;bottom:18px;height:48px;background:var(--wine);display:flex;align-items:center;padding-left:26px;color:var(--white);font-weight:600;font-size:22px;gap:10px}
.phone-bar svg{width:26px;height:26px}

/* inside: more about */
.panel--more{background:var(--crimson);color:var(--white)}
.photo--man{position:absolute;left:0;right:0;top:0;height:165px;background:radial-gradient(circle at 35% 55%,#e0707a 0%,#c9a9a4 30%,#d5d3d0 65%,#bfbcb8 100%)}
.more-body{position:absolute;left:30px;right:30px;top:190px;font-size:7.8px;line-height:1.3}
.more-body h2{font-size:17px;font-weight:600;line-height:1.05;margin-bottom:12px}
.more-body p{margin-bottom:12px}
.more-body h4{font-size:8.5px;font-weight:600;margin-bottom:5px}
.more-body li{margin-bottom:2px}
.notch{position:absolute;left:50px;top:158px;width:16px;height:16px;background:var(--crimson);transform:rotate(45deg)}

/* inside: types */
.panel--types{background:var(--purple)}
.types-top{position:absolute;left:0;right:0;top:0;height:262px;background:var(--blue);color:var(--white);padding:20px 28px 0 30px}
.types-top h2{font-size:19px;font-weight:700;line-height:1.02}
.types-top .tag{font-size:10px;margin:6px 0 8px}
.types-top ul{font-size:7.6px;line-height:1.22}
.types-top li{margin-bottom:1px}
.divider{position:absolute;left:0;right:0;top:262px;height:6px;background:var(--white)}
.diag{position:absolute;left:30px;right:28px;top:282px;color:var(--white);font-size:7.6px;line-height:1.3}
.diag h2{font-size:17px;font-weight:500;line-height:1.1;margin-bottom:8px}
.diag li{margin-bottom:5px}

/* treatments */
.panel--treat{background:var(--purple);color:var(--white)}
.photo--clipboard{position:absolute;left:0;right:0;top:0;height:150px;background:linear-gradient(160deg,#f3f1f0 0%,#cfc4bd 55%,#8e7b6f 100%)}
.treat-card{position:absolute;left:62px;top:30px;width:256px;height:94px;background:var(--white);border:6px solid #2b5d80;border-radius:6px;display:flex;align-items:center;justify-content:center;color:var(--crimson);font-size:21px;font-weight:600}
.life{position:absolute;left:0;right:0;top:150px;height:128px;background:var(--coral);padding:18px 26px 0;font-size:8.2px;line-height:1.2}
.life h4{font-size:9.5px;font-weight:600;margin-bottom:6px}
.treat-divider{position:absolute;left:0;right:0;top:278px;height:5px;background:var(--white)}
.monitors{position:absolute;left:26px;right:24px;top:294px;font-size:7.6px;line-height:1.25}
.monitors li{margin-bottom:4px}
</style>
</head>
<body>

<section class="spread spread--outside" aria-label="Brochure outside">
  <article class="panel panel--treat-detail">
    <div class="group">
      <h3>MEDICATIONS:</h3>
      <ul class="bullets">
        <li><b>Beta blockers:</b> Are blood pressure medications that also slow the heart rate down.</li>
        <li><b>Calcium channel blockers:</b> Are blood pressure medications that also slow the heart rate down</li>
        <li><b>Digoxin:</b> Is a medication that can slow the heart rate</li>
        <li><b>Anti-Arrhythmic:</b> Strong medications that work to calm the electrical system of the heart.</li>
        <li><b>Blood thinners:</b> May be used with some arrhythmias such as atrial fibrillation to help reduce the risk for stroke.</li>
      </ul>
    </div>
    <div class="group">
      <h3>PROCEDURES:</h3>
      <ul class="bullets">
        <li><b>Cardioversion:</b> The patient is put to sleep and the electrical energy is applied to the body to reset the heart rhythm back to normal.</li>
        <li><b>Ablation:</b> Electrical specialist takes small tubes called catheters up to the heart to find the abnormal rhythm. They then fix the abnormal rhythm by applying high energy to the problem spot which changes that area so that it not longer causes the problem.</li>
      </ul>
    </div>
    <div class="group">
      <h3>IMPLANTABLE DEVICES :</h3>
      <ul class="bullets">
        <li><b>Vigil Implant:</b> Small monitor implanted under the skin to monitor the heart rhythm for several years.</li>
        <li><b>Pacemaker:</b> Insertion of a small computer under the skin with wires attached to the heart to prevent the heat from beating too slow.</li>
        <li><b>Defibrillator:</b> Insertion of a small computer under the skin with wires attached to the heart. This computer watches all the heart beats and "shocks" the heart back to normal if a bad rhythm occurs.</li>
        <li><b>Cardiac Resynchronization Therapy (CRT):</b> A special type of pacemaker that paces both the left and right side of the heart which can make a weak heart stronger in some circumstances.</li>
        <li><b>Sealguard Device:</b> Place a plug like device in a part of the heart know as the left atrial appendage to help reduce the risk of stroke from atrial fibrillation.</li>
      </ul>
    </div>
    <div class="strip"></div>
  </article>

  <article class="panel panel--about">
    <div class="photo photo--chest" role="img" aria-label="Photo of a man in a blue shirt clutching his chest, with a glowing red heart and heartbeat line"></div>
    <div class="about-overlay"></div>
    <div class="ghost" style="left:110px;top:250px">ARRHYTHMIAS</div>
    <div class="about-body">
      <h2><span>ABOUT</span>ARRHYTHMIAS:</h2>
      <p>Arrhythmias are disorders of the electrical system of the heart.<br>A common arrhythmia is atrial fibrillation.</p>
      <div class="rule"></div>
      <h4>WHAT TO WATCH FOR:</h4>
      <ul class="bullets">
        <li>Flutters or skipping sensation</li>
        <li>Racing heart beat</li>
        <li>Lightheaded spells or passing out</li>
        <li>Trouble breathing</li>
      </ul>
      <div class="rule"></div>
      <h4>HOW TO DIAGNOSE:</h4>
      <ul class="bullets">
        <li>EKG</li><li>Heart monitor</li><li>EP study</li>
      </ul>
      <h4>HOW TO TREAT:</h4>
      <ul class="bullets">
        <li>Medications</li><li>Lifestyle change</li><li>Ablation</li><li>Devices</li>
      </ul>
    </div>
    <div class="about-foot">Larkmoor Cardiology and Vascular Medicine and located at 4512 Colby Road, Suites 300 &amp; 400, Winchester, VA 22601.</div>
    <div class="strip"></div>
  </article>

  <article class="panel panel--cover">
    <div class="photo photo--chest" role="img" aria-label="Cover photo of a man holding his chest with a glowing red heartbeat graphic"></div>
    <div class="ghost" style="left:-270px;top:250px">ARRHYTHMIAS</div>
    <h1 class="vertical">ARRHYTHMIAS</h1>
    <div class="phone-bar">
      <svg viewBox="0 0 26 26" aria-hidden="true"><circle cx="13" cy="13" r="12" fill="#f28a98"/><path d="M9 7l2.5 0 1 3-1.6 1.2a8 8 0 0 0 3.9 3.9L16 13.5l3 1v2.5c0 .8-.7 1.5-1.5 1.5C12 18.5 7.5 14 7.5 8.5 7.5 7.7 8.2 7 9 7z" fill="#fff"/></svg>
      540-555-0187
    </div>
    <div class="strip"></div>
  </article>
</section>

<section class="spread spread--inside" aria-label="Brochure inside">
  <article class="panel panel--more">
    <div class="photo--man" role="img" aria-label="Photo of a man in a grey t-shirt pressing his hand to his chest, with red highlight over the heart"></div>
    <div class="notch"></div>
    <div class="more-body">
      <h2>MORE ABOUT<br>ARRHYTHMIA</h2>
      <p>Arrhythmia refers to an abnormality of the electrical system of the heart. This may result in the heart beating too fast or too slow or irregularly. If the heart is not beating correctly, then the heart may not pump as strong as it should. This can cause symptoms.</p>
      <h4>SYMPTOMS INCLUDE THINGS<br>SUCH AS:</h4>
      <ul class="bullets bullets--soft">
        <li>Skips or flutters in the chest.</li>
        <li>Racing heart beat</li>
        <li>Lightheaded spells</li>
        <li>Passing out spells</li>
        <li>Trouble breathing</li>
      </ul>
    </div>
  </article>

  <article class="panel panel--types">
    <div class="types-top">
      <h2>TYPES OF<br>ARRHYTHMIA<br>INCLUDE:</h2>
      <p class="tag">We Don't Get Paid Unless You Do!</p>
      <ul class="bullets">
        <li><b>Atrial fibrillation:</b> Top half of the heart is beating irregularly</li>
        <li><b>Bradycardia:</b> heart beat is too slow</li>
        <li><b>Conduction disorders:</b> Problems with the electrical cells in the heart</li>
        <li><b>Premature contractions:</b> Early extra heart beats</li>
        <li><b>Tachycardia:</b> abnormally fast heart rate</li>
        <li><b>Supra Ventricular Tachycardia (SVT):</b> Fast abnormal heart beat from the upper heart chambers.</li>
        <li><b>Ventricular Tachycardia:</b> Fast abnormal heart beat from the lower heart chambers</li>
        <li><b>Genetic disorders:</b> Inherited abnormalities in the electrical system that can run in families.</li>
      </ul>
    </div>
    <div class="divider"></div>
    <div class="diag">
      <h2>How to diagnose<br>arrhythmias:</h2>
      <ul class="bullets">
        <li><b>EKG:</b> shows the hearts rhythm and electrical pattern at one moment in time.</li>
        <li><b>Holter monitor:</b> Wear a monitor that records all your heart's electrical activity for 1 to 3 days.</li>
        <li><b>Event monitor:</b> Wear a monitor for up to a month that records your heart's activity when you push a button.</li>
      </ul>
    </div>
  </article>

  <article class="panel panel--treat">
    <div class="photo--clipboard" role="img" aria-label="Photo of a doctor holding a clipboard"></div>
    <div class="treat-card">TREATMENTS</div>
    <div class="life">
      <h4>LIFE STYLE CHANGES:</h4>
      <ul class="bullets bullets--blue">
        <li>Work on ideal weight</li>
        <li>Control blood pressure</li>
        <li>Avoid stimulants (Coffee, tea, caffeinated beverages, chocolate, over the counter stimulants such as pseudophed)</li>
        <li>Limit alcohol consumption</li>
        <li>Exercise</li>
        <li>Treat sleep apnea if present</li>
      </ul>
    </div>
    <div class="treat-divider"></div>
    <ul class="monitors bullets">
      <li><b>MCOT:</b> Wear a monitor that records all your heart's electrical activity for a month</li>
      <li><b>Vigil:</b> Small implant under the skin that can record all the heart's electrical activity for a few years.</li>
      <li><b>Tilt Table:</b> Test where blood pressure and heart rate are recorded as you are slowly raised on a table from flat to nearly upright.</li>
      <li><b>EP study:</b> Procedure where an electrical specialist places specialized catheters (small tubes the size of coffee straws) into the heart to analyze the heart's electrical system.</li>
    </ul>
  </article>
</section>

</body>
</html>
```